Website for BrightlineLabs presentation

We need a new website, ideally as a wordpress there, for BrightlineLabs - we focus on machine learning, big data, data science and data analytics. This website should have two main sections - team presentation, introduction and offered services as static pages, and a blog section.

Target Market(s)

Companies which would like to hire the consultants for data science

Industry/Entity Type

Data Service

Font styles to use
Sans Serif

Colors

Designer to choose colors to be used in the design.

Requirements
Must have
• Wordpress template, blog and presentation pages, nice background images, incorporate the existing logo from brief
Nice to have
• match the word and ppt existing templates for brightline labs

```html
<!DOCTYPE html>
<html lang="en">
<head>
<meta charset="utf-8">
<title>Brightline Labs</title>
<link rel="stylesheet" href="https://fonts.googleapis.com/css2?family=Lato:wght@400;700;900&family=Oswald:wght@500;600&display=swap">
<style>
:root{
  --blue:#1389c8;
  --blue-deep:#0b5f97;
  --blue-dark:#073c66;
  --blue-soft:#4ea9db;
  --blue-pale:#a9d5ee;
  --white:#ffffff;
  --ink:#555a60;
  --line:#e6e8ea;
  --charcoal:#3b3d40;
}
*{box-sizing:border-box;margin:0;padding:0}
html,body{width:1200px;height:2305px;overflow:hidden}
body{position:relative;background:var(--white);font-family:"Lato",sans-serif;color:var(--ink)}
.backdrop{position:absolute;left:0;top:0}

/* top navigation */
.topbar{position:absolute;left:0;top:17px;width:1200px;height:50px}
.main-nav{position:absolute;left:80px;top:13px;display:flex;align-items:center;font-size:17px;color:var(--white);white-space:nowrap}
.main-nav a{color:var(--white);text-decoration:none}
.main-nav .sep{display:inline-block;width:2px;height:20px;background:rgba(255,255,255,.8);margin:0 44px}
.top-phone{position:absolute;left:815px;top:12px;display:flex;align-items:center;gap:10px;color:var(--white);font-size:19px;font-weight:700;white-space:nowrap}
.login-btn{position:absolute;left:998px;top:0;width:124px;height:50px;border:2px solid var(--white);border-radius:25px;display:flex;align-items:center;justify-content:center;gap:10px;color:var(--white);font-size:18px}

/* hero */
.hero{position:absolute;left:77px;top:83px;width:1045px;height:678px;box-shadow:0 30px 30px -18px rgba(0,0,0,.28)}
.hero-photo{position:absolute;inset:0;background:
  radial-gradient(ellipse at 70% 30%,rgba(60,150,200,.55),transparent 60%),
  linear-gradient(160deg,#0f4f7e 0%,#0a3457 45%,#0b2440 100%)}
.brand-tag{position:absolute;left:388px;top:0;width:268px;height:163px;background:var(--white);clip-path:polygon(0 0,100% 0,100% 78%,50% 100%,0 78%);display:flex;align-items:center;justify-content:center;gap:12px;padding-bottom:28px}
.brand-dot{width:22px;height:22px;border-radius:50%;background:var(--blue)}
.brand-name{font-weight:900;font-size:27px;line-height:1.05;color:var(--blue)}
.hero-copy{position:absolute;left:488px;top:275px;width:540px;color:var(--white)}
.hero-title{font-weight:900;font-size:49px;letter-spacing:1px;line-height:1;white-space:nowrap}
.hero-text{margin-top:22px;font-size:17.5px;font-weight:700;line-height:29px}
.btn-hex{display:flex;align-items:center;justify-content:center;height:62px;font-size:19px;white-space:nowrap;text-decoration:none;clip-path:polygon(12% 0,88% 0,100% 50%,88% 100%,12% 100%,0 50%)}
.hero .btn-hex{position:absolute;left:488px;top:470px;width:164px;background:var(--blue);color:var(--white)}

/* section headings */
.section-head{position:absolute;left:0;width:1200px;display:flex;align-items:center;justify-content:center;gap:22px;font-family:"Oswald",sans-serif;font-weight:600;font-size:40px}
.section-head::before,.section-head::after{content:"";width:65px;height:2px;background:currentColor;opacity:.4}
.services-head{top:820px;color:var(--blue)}

/* services */
.service{position:absolute;top:917px;width:240px;height:396px;border:2px solid var(--line);border-radius:120px;text-align:center;background:var(--white)}
.service.featured{background:var(--blue);border-color:var(--blue)}
.service-icon{position:absolute;left:63px;top:40px;width:114px;height:114px;border-radius:50%;background:var(--blue);display:flex;align-items:center;justify-content:center}
.service.featured .service-icon{background:var(--white)}
.service-title{position:absolute;left:0;top:176px;width:100%;font-size:23px;font-weight:400;letter-spacing:.5px;color:var(--blue)}
.service-text{position:absolute;left:26px;top:221px;width:184px;font-size:14.5px;line-height:25px;color:var(--ink)}
.service.featured .service-title,.service.featured .service-text{color:var(--white)}

/* about */
.about{position:absolute;left:77px;top:1376px;width:1045px;height:467px;background:var(--blue-soft)}
.about-head{top:46px;width:1045px;color:var(--white)}
.about-text{position:absolute;left:75px;top:136px;width:625px;font-size:14.3px;line-height:25px;color:var(--white)}
.about .btn-hex{position:absolute;left:73px;top:303px;width:165px;background:var(--white);color:var(--blue)}
.about-badge{position:absolute;left:754px;top:150px;width:208px;height:208px;border-radius:50%;background:var(--white);box-shadow:0 0 0 6px var(--blue-soft),0 0 0 8px rgba(255,255,255,.7);display:flex;align-items:center;justify-content:center;text-align:center}
.about-badge span{font-weight:900;font-size:24px;line-height:1.1;color:var(--blue)}

/* footer */
.footer-col{position:absolute;top:1905px;color:var(--white)}
.footer-title{font-family:"Oswald",sans-serif;font-weight:500;font-size:24px;margin-bottom:24px}
.contact-line{display:flex;gap:16px;font-size:15px;line-height:24px;margin-bottom:14px}
.contact-line svg{flex:0 0 20px;margin-top:3px}
.nav-list{list-style:none;font-size:15px}
.nav-list li{display:flex;align-items:center;gap:14px;margin-bottom:18px}
.nav-list li::before{content:"";width:6px;height:6px;background:var(--white)}
.post{display:flex;gap:22px;align-items:center;margin-bottom:16px}
.post-thumb{width:80px;height:80px;border-radius:50%;border:3px solid var(--white);background:linear-gradient(150deg,#6f8aa5,#2d4a66)}
.post-text{font-size:14.5px;line-height:25px;width:150px}
.post-date{font-style:italic;font-size:14px}
.newsletter-text{font-size:14.5px;line-height:25px;width:265px}
.subscribe{margin-top:24px;display:flex;width:260px;height:46px;border-radius:23px;overflow:hidden;background:var(--white)}
.subscribe span{flex:1;padding-left:16px;line-height:46px;font-size:14px;color:#333}
.subscribe b{width:60px;background:var(--blue);display:flex;align-items:center;justify-content:center}

.bottombar{position:absolute;left:0;top:2220px;width:1200px;height:85px;background:var(--blue)}
.copyright{position:absolute;left:80px;top:33px;font-size:14px;color:var(--white)}
.copyright strong{font-weight:900}
.social{position:absolute;left:918px;top:18px;display:flex;gap:10px}
.social span{width:48px;height:48px;border:2px solid var(--white);border-radius:50%}
</style>
</head>
<body>

<svg class="backdrop" width="1200" height="2305" viewBox="0 0 1200 2305" aria-hidden="true">
  <defs>
    <linearGradient id="topBlue" x1="0" y1="0" x2="0" y2="1">
      <stop offset="0" stop-color="#1b7fbf"/>
      <stop offset="1" stop-color="#1a8ccf"/>
    </linearGradient>
  </defs>
  <rect width="1200" height="470" fill="url(#topBlue)"/>
  <path d="M0,420 Q600,330 1200,420 L1200,640 Q600,520 0,640 Z" fill="#5aaee0"/>
  <path d="M0,510 Q600,420 1200,510 L1200,640 Q600,540 0,640 Z" fill="#8cc8ea"/>
  <path d="M0,580 Q600,500 1200,580 L1200,700 Q600,560 0,700 Z" fill="#c9e5f5"/>
  <path d="M0,1620 Q600,1520 1200,1620 L1200,1760 L0,1760 Z" fill="#a9d5ee"/>
  <path d="M0,1680 Q600,1600 1200,1680 L1200,1760 L0,1760 Z" fill="#5aaee0"/>
  <path d="M0,1760 Q600,1650 1200,1760 L1200,2220 L0,2220 Z" fill="#3b3d40"/>
</svg>

<header class="topbar">
  <nav class="main-nav">
    <a href="#">Home</a><span class="sep"></span>
    <a href="#">About</a><span class="sep"></span>
    <a href="#">Services</a><span class="sep"></span>
    <a href="#">Blog</a><span class="sep"></span>
    <a href="#">Contact</a>
  </nav>
  <div class="top-phone">
    <svg width="22" height="22" viewBox="0 0 24 24"><path fill="#fff" d="M6.6 10.8a15 15 0 006.6 6.6l2.2-2.2c.3-.3.7-.4 1-.2 1.1.4 2.3.6 3.6.6.6 0 1 .4 1 1V20c0 .6-.4 1-1 1A17 17 0 013 4c0-.6.4-1 1-1h3.5c.6 0 1 .4 1 1 0 1.3.2 2.5.6 3.6.1.3 0 .7-.2 1z"/></svg>
    555-010-2468
  </div>
  <a class="login-btn">
    <svg width="22" height="22" viewBox="0 0 24 24" fill="none" stroke="#fff" stroke-width="2"><circle cx="12" cy="12" r="10"/><path d="M5 12h10M11 8l4 4-4 4"/></svg>
    Login
  </a>
</header>

<section class="hero">
  <div class="hero-photo" role="img" aria-label="Analyst holding a tablet in front of a glowing world network backdrop"></div>
  <div class="brand-tag"><span class="brand-dot"></span><span class="brand-name">BRIGHTLINE<br>LABS</span></div>
  <div class="hero-copy">
    <h1 class="hero-title">BRIGHTLINE LABS</h1>
    <p class="hero-text">Lorem Ipsum is simply dummy text of the printing and typesetting industry. Lorem Ipsum has been the industry's standard dummy text ever since the 1500s.</p>
  </div>
  <a class="btn-hex">CONTACT US</a>
</section>

<h2 class="section-head services-head">OUR SERVICES</h2>

<article class="service" style="left:77px">
  <div class="service-icon">
    <svg width="52" height="52" viewBox="0 0 52 52" fill="none" stroke="#fff" stroke-width="2"><rect x="8" y="8" width="36" height="24" rx="3"/><circle cx="20" cy="20" r="6"/><path d="M32 16h6M32 22h6M26 32v8M16 44h20"/></svg>
  </div>
  <h3 class="service-title">Machine learning</h3>
  <p class="service-text">Lorem Ipsum is simply dummy text of the printing and typesetting industry. Lorem Ipsum has been the industry's standard...(+)</p>
</article>

<article class="service" style="left:345px">
  <div class="service-icon">
    <svg width="52" height="52" viewBox="0 0 52 52" fill="none" stroke="#fff" stroke-width="2"><path d="M14 26a8 8 0 010-16 11 11 0 0121 2 7 7 0 011 14z"/><rect x="12" y="30" width="10" height="10"/><rect x="30" y="30" width="10" height="10"/><rect x="21" y="38" width="10" height="10"/></svg>
  </div>
  <h3 class="service-title">Big data</h3>
  <p class="service-text">Lorem Ipsum is simply dummy text of the printing and typesetting industry. Lorem Ipsum has been the industry's standard...(+)</p>
</article>

<article class="service featured" style="left:614px">
  <div class="service-icon">
    <svg width="52" height="52" viewBox="0 0 52 52" fill="none" stroke="#333" stroke-width="2"><rect x="14" y="8" width="24" height="36" rx="3"/><circle cx="26" cy="26" r="6"/><path d="M4 16h10M4 36h10M38 16h10M38 36h10M26 2v6"/></svg>
  </div>
  <h3 class="service-title">Data science</h3>
  <p class="service-text">Lorem Ipsum is simply dummy text of the printing and typesetting industry. Lorem Ipsum has been the industry's standard...(+)</p>
</article>

<article class="service" style="left:883px">
  <div class="service-icon">
    <svg width="52" height="52" viewBox="0 0 52 52" fill="none" stroke="#fff" stroke-width="2"><path d="M6 44h40"/><rect x="10" y="32" width="6" height="12"/><rect x="20" y="26" width="6" height="18"/><rect x="30" y="30" width="6" height="14"/><rect x="40" y="20" width="6" height="24"/><path d="M12 24l10-8 10 6 12-12"/></svg>
  </div>
  <h3 class="service-title">Data analytics</h3>
  <p class="service-text">Lorem Ipsum is simply dummy text of the printing and typesetting industry. Lorem Ipsum has been the industry's standard...(+)</p>
</article>

<section class="about">
  <h2 class="section-head about-head">ABOUT US</h2>
  <p class="about-text">Lorem Ipsum is simply dummy text of the printing and typesetting industry. Lorem Ipsum has been the industry's standard dummy text ever since the 1500s, when an unknown printer took a galley of type and scrambled it to make a type specimen book. It has survived not only five centuries, but also the leap into electronic typesetting, remaining essentially unchanged. It was popularised in the 1960s with the release of Letraset sheets containing Lorem Ipsum passages, and more recently with desktop publishing software.</p>
  <a class="btn-hex">CONTACT US</a>
  <div class="about-badge"><span>BRIGHTLINE<br>LABS</span></div>
</section>

<div class="footer-col" style="left:80px">
  <h4 class="footer-title">GET IN TOUCH</h4>
  <div class="contact-line"><svg width="20" height="22" viewBox="0 0 24 24"><path fill="#fff" d="M12 2a7 7 0 00-7 7c0 5 7 13 7 13s7-8 7-13a7 7 0 00-7-7zm0 9.5A2.5 2.5 0 1112 6a2.5 2.5 0 010 5.5z"/></svg><span>123 Building Name, Street,<br>City, Country - Zip code</span></div>
  <div class="contact-line"><svg width="20" height="20" viewBox="0 0 24 24"><path fill="#fff" d="M6.6 10.8a15 15 0 006.6 6.6l2.2-2.2c.3-.3.7-.4 1-.2 1.1.4 2.3.6 3.6.6.6 0 1 .4 1 1V20c0 .6-.4 1-1 1A17 17 0 013 4c0-.6.4-1 1-1h3.5c.6 0 1 .4 1 1 0 1.3.2 2.5.6 3.6.1.3 0 .7-.2 1z"/></svg><span>(555)-010-2468</span></div>
  <div class="contact-line"><svg width="20" height="16" viewBox="0 0 24 18" fill="none" stroke="#fff" stroke-width="2"><rect x="1" y="1" width="22" height="16"/><path d="M1 1l11 9 11-9"/></svg><span>info@brightlinelabs.com</span></div>
</div>

<div class="footer-col" style="left:352px">
  <h4 class="footer-title">NAVIGATION</h4>
  <ul class="nav-list"><li>Home</li><li>About</li><li>Services</li><li>Blog</li><li>Contact</li></ul>
</div>

<div class="footer-col" style="left:567px">
  <h4 class="footer-title">BLOG POST</h4>
  <div class="post">
    <div class="post-thumb" role="img" aria-label="Blog post thumbnail photo of a team meeting"></div>
    <div class="post-text">Lorem Ipsum is simply dummy text of the.<br><span class="post-date">03 July 2018</span></div>
  </div>
  <div class="post">
    <div class="post-thumb" role="img" aria-label="Blog post thumbnail photo of a data workspace"></div>
    <div class="post-text">Lorem Ipsum is simply dummy text of the.<br><span class="post-date">03 July 2018</span></div>
  </div>
</div>

<div class="footer-col" style="left:863px">
  <h4 class="footer-title">NEWSLETTER</h4>
  <p class="newsletter-text">Lorem Ipsum is simply dummy text of the printing and typesetting industry. Lorem Ipsum has been the industry's.</p>
  <div class="subscribe"><span>Email</span><b><svg width="24" height="22" viewBox="0 0 24 22"><path fill="#fff" d="M0 9L24 0 18 22 11 14 20 4 8 12z"/></svg></b></div>
</div>

<footer class="bottombar">
  <p class="copyright">Copyright © <strong>BRIGHTLINE LABS</strong> - 2018 . All Right Reserved</p>
  <div class="social" aria-label="Social links"><span></span><span></span><span></span><span></span></div>
</footer>

</body>
</html>
```